Brovanek Data Yellow rose letterhead

I have a new logo for my company but in its current form it is too large to be used on letterhead or as a email signature. I need to have the designer use elements from the current logo and create something close to the original but more suited for smaller items.
Updates

I just uploaded a copy of our logo that does not have the weathered affect. Thanks

Reason: More time for revisions

Industry/Entity Type

It Company

Requirements
Must have
• The design must maintain the visual effect of the current logo. It needs to include the yellow rose and the name of the company.
Nice to have
• It would be nice to maintain the stamp theme and incorporate my name, address, phone, email. etc.

```html
<!DOCTYPE html>
<html lang="en">
<head>
<meta charset="utf-8">
<title>Brovanek Data Letterhead</title>
<link rel="stylesheet" href="https://fonts.googleapis.com/css2?family=Questrial&display=swap">
<style>
  :root {
    --backdrop: #e9e6e1;
    --paper: #ffffff;
    --teal: #3cb8bf;
    --brand-brown: #4b3b34;
    --brand-orange: #f0942a;
    --ink: #1c1c1c;
  }
  * { margin: 0; padding: 0; box-sizing: border-box; }
  html, body {
    width: 1054px;
    height: 1200px;
    overflow: hidden;
    background: var(--backdrop);
  }
  .letterhead {
    position: absolute;
    left: 127px;
    top: 35px;
    width: 800px;
    height: 1130px;
    background: var(--paper);
    box-shadow: 0 2px 10px rgba(0, 0, 0, 0.15);
    overflow: hidden;
    font-family: "Questrial", sans-serif;
  }
  .side-band {
    position: absolute;
    inset: 0;
    width: 800px;
    height: 1130px;
  }
  .side-band path { fill: var(--teal); }
  .brand-mark {
    position: absolute;
    left: 552px;
    top: 78px;
    display: flex;
    align-items: center;
    gap: 12px;
  }
  .brand-square {
    width: 26px;
    height: 26px;
    background: var(--brand-orange);
  }
  .brand-name {
    font-size: 28px;
    color: var(--brand-brown);
    letter-spacing: 0.5px;
    white-space: nowrap;
  }
  .sender-details {
    position: absolute;
    left: 41px;
    top: 985px;
    font-style: normal;
    font-size: 18px;
    line-height: 24px;
    color: var(--ink);
  }
  .sender-name { font-size: 16px; }
</style>
</head>
<body>
  <main class="letterhead">
    <svg class="side-band" viewBox="0 0 800 1130" aria-hidden="true">
      <path d="M736,0 L800,0 L800,1130 L705,1130 C716,900 738,560 736,0 Z"/>
    </svg>

    <div class="brand-mark">
      <span class="brand-square"></span>
      <span class="brand-name">Brovanek Data</span>
    </div>

    <address class="sender-details">
      <div class="sender-name">Mara Kellison, PhD</div>
      <div>418 W Cedar Hollow Rd, Ste 1207</div>
      <div>Lampasas, TX 76550</div>
      <div>1-800-555-0147</div>
      <div>mara@brovanek-data.com</div>
    </address>
  </main>
</body>
</html>
```